Book Cover with this title and sub title
Where Auntie Found Her Quiet Orchard
A small guide to be wise with your savings and look after the planet.
Walter P. Brunk Ph. D.
Ellen R. Brunk
Picture below would be on the entire front cover. Words somehow incorporated for easy reading.

```html
<!DOCTYPE html>
<html lang="en">
<head>
<meta charset="utf-8">
<title>Where Auntie Found Her Quiet Orchard — Book Cover</title>
<link href="https://fonts.googleapis.com/css2?family=Bebas+Neue&family=Lora:ital,wght@1,400&display=swap" rel="stylesheet">
<style>
  :root {
    --stage: #3a3a3a;
    --paper: #ffffff;
    --navy: #152a47;
    --orange: #ff7f00;
    --orange-deep: #c0560f;
    --rule: #f07a14;
    --band: #d45f0c;
    --tagline: #e8622a;
    --petal: #f7cc14;
    --petal-deep: #d9a10a;
    --earth: #6b5a3e;
  }
  html, body {
    margin: 0;
    width: 1200px;
    height: 1200px;
    overflow: hidden;
    background: var(--stage);
  }
  .cover {
    position: absolute;
    left: 202px;
    top: 0;
    width: 795px;
    height: 1200px;
    background: var(--paper);
    overflow: hidden;
  }
  .title-block {
    position: absolute;
    left: 0;
    top: 0;
    width: 795px;
    height: 466px;
  }
  .title-small, .title-large {
    font-family: "Bebas Neue", "Oswald", sans-serif;
    fill: var(--navy);
  }
  .title-feature {
    font-family: "Bebas Neue", "Oswald", sans-serif;
    fill: url(#featureGradient);
  }
  .title-rule {
    stroke: var(--rule);
    stroke-width: 3;
  }
  .photo-band {
    position: absolute;
    left: 0;
    top: 466px;
    width: 795px;
    height: 489px;
    box-sizing: border-box;
    border-top: 8px solid var(--band);
    border-bottom: 8px solid var(--band);
  }
  .photo-area {
    width: 100%;
    height: 100%;
    background:
      radial-gradient(ellipse 60% 65% at 58% 60%, #ffd83a 0%, var(--petal) 45%, var(--petal-deep) 75%, transparent 92%),
      linear-gradient(135deg, #7a8a55 0%, var(--earth) 35%, #8a7550 100%);
  }
  .tagline {
    position: absolute;
    left: 0;
    top: 972px;
    width: 795px;
    margin: 0;
    text-align: center;
    font-family: "Lora", "Georgia", serif;
    font-style: italic;
    font-size: 33px;
    line-height: 42px;
    color: var(--tagline);
  }
  .authors {
    position: absolute;
    left: 0;
    top: 1108px;
    width: 795px;
    display: flex;
    justify-content: center;
    align-items: center;
    gap: 18px;
    font-family: "Bebas Neue", "Oswald", sans-serif;
    font-size: 50px;
    line-height: 1;
    letter-spacing: 1.5px;
    color: var(--navy);
  }
  .author-divider {
    width: 4px;
    height: 46px;
    background: var(--tagline);
  }
</style>
</head>
<body>
  <main class="cover">
    <svg class="title-block" viewBox="0 0 795 466" aria-labelledby="bookTitle">
      <title id="bookTitle">Where Auntie Found Her Quiet Orchard</title>
      <defs>
        <linearGradient id="featureGradient" x1="0" y1="0" x2="1" y2="0">
          <stop offset="0" stop-color="#c0560f"/>
          <stop offset="0.35" stop-color="#ff7f00"/>
          <stop offset="0.65" stop-color="#ff7f00"/>
          <stop offset="1" stop-color="#c0560f"/>
        </linearGradient>
      </defs>
      <text class="title-small" x="397.5" y="98" text-anchor="middle" font-size="82">WHERE</text>
      <text class="title-large" x="397.5" y="200" text-anchor="middle" font-size="128" textLength="690" lengthAdjust="spacing">AUNTIE FOUND</text>
      <line class="title-rule" x1="53" y1="246" x2="269" y2="246"/>
      <text class="title-small" x="397.5" y="273" text-anchor="middle" font-size="72">HER QUIET</text>
      <line class="title-rule" x1="526" y1="246" x2="742" y2="246"/>
      <text class="title-feature" x="397.5" y="430" text-anchor="middle" font-size="192" textLength="690" lengthAdjust="spacing">ORCHARD</text>
    </svg>

    <div class="photo-band">
      <div class="photo-area" role="img" aria-label="Close-up photograph of a honeybee gathering pollen on a bright yellow dandelion flower, with green leaves and earth behind"></div>
    </div>

    <p class="tagline">A small guide to be wise with your savings<br>and look after the planet</p>

    <div class="authors">
      <span class="author-name">Walter P. Brunk Ph. D.</span>
      <span class="author-divider" aria-hidden="true"></span>
      <span class="author-name">Ellen R. Brunk</span>
    </div>
  </main>
</body>
</html>
```